Wordpress Website - for cutting edge Artificial Intelligence company

We need a wordpress web site for our company Varlomex.

Objective:
- To promote our software products to potential customers (e.g. large corporations)
- To promote our software products to potential partners (e.g. software makers who want to bundle our software inside their products)
- To promote our company to potential Investors (venture capital funds, angel investors, etc.)

Sample content and proposed structure can be found in the attached file.
Company logo is also attached.

The Plover logo should only be used in the section relating to the Plover Product (e.g. Plover Text & Plover Speech)

Target Market(s)

Core Target Market:
- Large corporations (e.g. Major Banks, Retailers & Pharmaceutical companies) who could buy our software

Industry/Entity Type

Software

Coding

Coded - Design and coding required

Font styles to use
Sans Serif

Colors
ffffff
ec1f27
000000
757575
dfdfdf
9bcb3c

Requirements
Must have
• Functionality:
• - Designed in Wordpress (using tools from wordpress.org, not hosted on wordpress.com)
• - Must have a user friendly CMS module for us to make updates easily
• - Must be designed to look great across different devices
• - Must be designed to look great in English and Chinese (as well as other future languages).

```html
<!DOCTYPE html>
<html lang="en">
<head>
<meta charset="utf-8">
<title>Varlomex — Natural Intelligence</title>
<link rel="stylesheet" href="https://fonts.googleapis.com/css2?family=Jost:wght@400;500;600&family=Roboto:wght@400;500&family=Raleway:wght@400;500;600&display=swap">
<style>
:root{
  --red:#ec1f27;
  --red-dark:#b8141b;
  --black:#000000;
  --ink:#222222;
  --grey:#757575;
  --light:#dfdfdf;
  --white:#ffffff;
  --footer:#1e1e1e;
}
*{box-sizing:border-box;margin:0;padding:0}
html,body{width:1200px;height:2250px;overflow:hidden;background:var(--white)}
body{position:relative;font-family:"Roboto",Arial,sans-serif;color:var(--ink)}
.abs{position:absolute}

/* header */
.topline{left:0;top:0;width:1200px;height:5px;background:var(--red)}
.brand{left:98px;top:22px;font-family:"Jost",sans-serif;font-weight:500;font-size:44px;letter-spacing:1px;color:var(--red);line-height:1}
.social-top{top:29px;display:flex;gap:7px;left:697px}
.social-top span{width:38px;height:38px;border-radius:50%;display:block}
.search{left:880px;top:30px;width:220px;height:35px;border:1px solid #bdbdbd;border-radius:3px;font-size:16px;color:var(--grey);padding:7px 10px;font-family:"Roboto",sans-serif}
.search svg{position:absolute;right:10px;top:10px}

/* navigation */
.nav{left:0;top:93px;width:1200px;height:59px;background:linear-gradient(#f03a40,var(--red))}
.nav-item{position:absolute;top:0;height:59px;line-height:59px;font-size:16px;font-weight:500;color:var(--white);text-transform:uppercase}
.nav-item.active{background:var(--red-dark);padding:0 20px}
.lang{position:absolute;left:954px;top:12px;width:147px;height:36px;border:1px solid var(--white);color:var(--white);font-size:15px;font-weight:500;line-height:34px;padding-left:12px}

/* hero */
.hero{left:0;top:152px;width:1200px;height:531px;clip-path:polygon(0 0,100% 0,100% 490px,50% 531px,0 490px);
  background:radial-gradient(ellipse 420px 300px at 50% 48%,#f2b233 0%,#c7321a 30%,#5a0d0b 62%,#1a0a0a 100%)}
.hero-band{left:150px;top:285px;width:900px;height:72px;background:rgba(30,20,20,.55)}
.hero-title{left:0;width:1200px;top:296px;text-align:center;font-family:"Jost",sans-serif;font-weight:500;font-size:42px;color:var(--white);letter-spacing:.5px}
.hero-sub{left:0;width:1200px;top:372px;text-align:center;font-family:"Jost",sans-serif;font-weight:500;font-size:27px;color:var(--white)}
.btn{height:50px;line-height:46px;text-align:center;font-size:18px;color:var(--white);border:2px solid var(--white);text-transform:uppercase}
.btn-red{left:424px;top:453px;width:185px;background:var(--red)}
.btn-ghost{left:625px;top:453px;width:151px;background:rgba(0,0,0,.25)}

/* section headings */
.heading{left:0;width:1200px;text-align:center;font-family:"Jost",sans-serif;font-weight:500;font-size:33px;color:var(--ink)}
.heading em{font-style:normal;color:var(--red)}
.rule{height:2px;background:var(--red)}

/* news */
.card{width:318px;height:225px;overflow:hidden}
.card-caption{position:absolute;left:0;bottom:0;width:100%;height:55px;background:rgba(236,31,39,.92);color:var(--white);font-size:20px;font-weight:500;text-align:center;line-height:55px;text-transform:uppercase}
.card-feature{position:absolute;left:9px;top:9px;width:300px;height:207px;background:var(--red);color:var(--white);text-align:center}
.card-feature h3{font-weight:400;font-size:20px;margin-top:56px}
.card-feature p{font-size:17px;margin-top:8px}
.card-feature .more{display:inline-block;margin-top:22px;border:2px solid var(--white);font-size:13px;font-weight:500;padding:9px 14px}

/* testimonials */
.stories{left:0;top:1343px;width:1200px;height:517px;clip-path:polygon(0 0,100% 0,100% 465px,50% 517px,0 465px);
  background:linear-gradient(160deg,#e8232b 0%,#d81a22 50%,#ee2a31 100%)}
.stories-title{left:0;width:1200px;top:1378px;text-align:center;font-family:"Jost",sans-serif;font-weight:500;font-size:30px;color:var(--white);letter-spacing:.5px}
.avatar{width:144px;height:144px;border-radius:50%;border:3px solid var(--white);box-shadow:0 0 0 3px rgba(255,255,255,.25);background:radial-gradient(circle at 50% 40%,#d9d4cf,#8b8580 70%,#4a4542)}
.person{width:340px;text-align:center;color:var(--white)}
.person h4{font-size:22px;font-weight:500}
.person p{font-size:13.5px;line-height:22.5px;margin-top:10px;font-family:"Raleway",sans-serif}
.person .role{font-weight:600;margin-top:10px}

/* footer */
.footer{left:0;top:1808px;width:1200px;height:379px;background:var(--footer)}
.footer-brand{left:98px;top:2007px;font-family:"Jost",sans-serif;font-weight:500;font-size:38px;color:var(--white);letter-spacing:1px}
.col-title{font-family:"Jost",sans-serif;font-weight:500;font-size:19px;color:var(--white)}
.col-rule{height:1px;background:#8a8a8a}
.links{list-style:none;font-family:"Raleway",sans-serif;font-size:15px;color:var(--white)}
.links li{height:32px}
.links li::before{content:"›";margin-right:6px;font-size:17px}
.contact-icon{width:38px;height:38px;border-radius:50%;border:1.5px solid var(--white);display:flex;align-items:center;justify-content:center}
.contact-text{font-family:"Raleway",sans-serif;color:var(--white);font-size:13px;line-height:20px}
.contact-text b{font-weight:600;font-size:15px;display:block;margin-bottom:3px}
.field{border:1px solid #cfcfcf;border-radius:3px;color:var(--white);font-family:"Raleway",sans-serif;font-size:12px;padding:10px 12px}
.send{left:813px;top:2076px;width:119px;height:36px;background:var(--red);color:var(--white);border-radius:3px;font-family:"Raleway",sans-serif;font-size:12px;font-weight:500;text-align:center;line-height:36px}

/* bottom bar */
.bottombar{left:0;top:2187px;width:1200px;height:63px;background:var(--red)}
.copyright{left:98px;top:2208px;font-family:"Raleway",sans-serif;font-size:13.5px;color:var(--white)}
.social-bottom{left:948px;top:2202px;display:flex;gap:8px}
.social-bottom span{width:33px;height:33px;border-radius:50%;border:1.5px solid var(--white);display:block}
</style>
</head>
<body>

<!-- header -->
<div class="abs topline"></div>
<div class="abs brand">VARLOMEX</div>
<div class="abs social-top">
  <span style="background:#3b5998"></span>
  <span style="background:#1da1f2"></span>
  <span style="background:#2a5b83"></span>
  <span style="background:#cb2027"></span>
</div>
<div class="abs search">Search
  <svg width="14" height="14" viewBox="0 0 14 14"><circle cx="6" cy="6" r="4.5" fill="none" stroke="#757575" stroke-width="1.8"/><line x1="9.3" y1="9.3" x2="13" y2="13" stroke="#757575" stroke-width="2"/></svg>
</div>

<!-- navigation -->
<nav class="abs nav">
  <div class="nav-item active" style="left:99px">Natural Intelligence</div>
  <div class="nav-item" style="left:348px">Products</div>
  <div class="nav-item" style="left:481px">Services</div>
  <div class="nav-item" style="left:604px">Partners</div>
  <div class="nav-item" style="left:732px">Contact Us</div>
  <div class="nav-item" style="left:876px">About</div>
  <div class="lang">Language: ENG
    <svg width="10" height="7" viewBox="0 0 10 7" style="margin-left:6px"><path d="M1 1l4 4 4-4" fill="none" stroke="#fff" stroke-width="1.6"/></svg>
  </div>
</nav>

<!-- hero -->
<div class="abs hero" role="img" aria-label="Glowing digital brain surrounded by streams of red binary code"></div>
<div class="abs hero-band"></div>
<h1 class="abs hero-title">PLOVER, BY VARLOMEX. THE NEW STANDARD IN</h1>
<div class="abs hero-sub">CONTACT CENTER CUSTOMER EXPERIENCE.</div>
<div class="abs btn btn-red">Request a Demo</div>
<div class="abs btn btn-ghost">Contact Us</div>
<svg class="abs" style="left:30px;top:393px" width="30" height="54" viewBox="0 0 30 54"><path d="M27 2L3 27l24 25" fill="none" stroke="#fff" stroke-width="2.5"/></svg>
<svg class="abs" style="left:1136px;top:393px" width="30" height="54" viewBox="0 0 30 54"><path d="M3 2l24 25L3 52" fill="none" stroke="#fff" stroke-width="2.5"/></svg>

<!-- recent news -->
<h2 class="abs heading" style="top:716px">RECENT <em>NEWS</em></h2>
<div class="abs rule" style="left:552px;top:769px;width:96px"></div>

<div class="abs card" style="left:99px;top:812px;background:linear-gradient(135deg,#dfe6ea,#9aa6ad 60%,#6b6258)" role="img" aria-label="Humanoid robot holding a gift box">
  <div class="card-caption">Consectetur Adipiscing Elit</div>
</div>
<div class="abs card" style="left:441px;top:812px;background:linear-gradient(135deg,#3a4250,#6a5a48 60%,#2c2a2a)" role="img" aria-label="Dark technology photograph behind a featured story">
  <div class="card-feature">
    <h3>MAURIS VITAE PORTA</h3>
    <p>Nulla rhoncus augue tellus erat</p>
    <div class="more">READ MORE</div>
  </div>
</div>
<div class="abs card" style="left:783px;top:812px;background:linear-gradient(135deg,#7fe0d9,#58c9c0 55%,#3a4a46)" role="img" aria-label="Android figure resting its chin on its hand">
  <div class="card-caption">Nulla Rhoncus Augue</div>
</div>
<div class="abs card" style="left:99px;top:1061px;background:linear-gradient(135deg,#5d6a72,#8c8f7e 55%,#4e5a44)" role="img" aria-label="Soldier wearing a head-mounted display with floating interface panels">
  <div class="card-caption">Nulla Ultricies Accumsan</div>
</div>
<div class="abs card" style="left:441px;top:1061px;background:linear-gradient(135deg,#9fc4e4,#6f9fcb 55%,#c8d6e2)" role="img" aria-label="Robot beside a blue circuit board">
  <div class="card-caption">Phasellus Laoreet Eros</div>
</div>
<div class="abs card" style="left:783px;top:1061px;background:linear-gradient(135deg,#eef4f7,#b9d4e2 55%,#2a9cc4)" role="img" aria-label="Hand touching a connected car interface">
  <div class="card-caption">Aenean Mattis Ante</div>
</div>

<!-- success stories -->
<div class="abs stories" role="img" aria-label="Red tinted city skyline background"></div>
<h2 class="abs stories-title">SUCCESS STORIES FROM OUR PARTNERS</h2>
<div class="abs rule" style="left:528px;top:1429px;width:144px;background:#fff"></div>

<div class="abs avatar" style="left:168px;top:1484px" role="img" aria-label="Portrait of Marcus"></div>
<div class="abs avatar" style="left:528px;top:1484px" role="img" aria-label="Portrait of Leonard"></div>
<div class="abs avatar" style="left:881px;top:1484px" role="img" aria-label="Portrait of Rowan Tate"></div>

<div class="abs person" style="left:70px;top:1640px">
  <h4>Marcus</h4>
  <p>Nemo enim ipsam voluptatem quia volup tas sit<br>aspernatur aut odit aut fugit, sed quia consequ.<br>magni dolores eos qui ratione.</p>
  <p class="role">- Manager</p>
</div>
<div class="abs person" style="left:430px;top:1640px">
  <h4>Leonard</h4>
  <p>Nemo enim ipsam voluptatem quia volup tas sit<br>aspernatur aut odit aut fugit, sed quia consequ.<br>magni dolores eos qui ratione.</p>
  <p class="role">- Manager</p>
</div>
<div class="abs person" style="left:783px;top:1640px">
  <h4>Rowan Tate</h4>
  <p>Nemo enim ipsam voluptatem quia volup tas sit<br>aspernatur aut odit aut fugit, sed quia consequ.<br>magni dolores eos qui ratione.</p>
  <p class="role">- Manager</p>
</div>

<!-- footer -->
<footer>
<div class="abs footer" style="clip-path:polygon(0 0,50% 52px,100% 0,100% 100%,0 100%);top:1808px"></div>
<div class="abs footer-brand">VARLOMEX</div>

<div class="abs col-title" style="left:393px;top:1895px">QUICK LINKS</div>
<div class="abs col-rule" style="left:393px;top:1932px;width:112px"></div>
<ul class="abs links" style="left:400px;top:1957px">
  <li>Home</li><li>Natural Intelligence</li><li>Services</li><li>Products</li><li>Partners</li><li>Contact Us</li>
</ul>

<div class="abs col-title" style="left:579px;top:1895px">CONTACT US</div>
<div class="abs col-rule" style="left:579px;top:1932px;width:112px"></div>
<div class="abs contact-icon" style="left:578px;top:1961px">
  <svg width="14" height="18" viewBox="0 0 14 18"><path d="M7 1a5.5 5.5 0 0 0-5.5 5.5C1.5 11 7 17 7 17s5.5-6 5.5-10.5A5.5 5.5 0 0 0 7 1z" fill="none" stroke="#fff" stroke-width="1.6"/><circle cx="7" cy="6.5" r="2" fill="#fff"/></svg>
</div>
<div class="abs contact-text" style="left:635px;top:1957px"><b>VARLOMEX,</b>Varlomex Canada Corp.<br>18 Alderway Ave., #310</div>
<div class="abs contact-icon" style="left:578px;top:2036px">
  <svg width="10" height="16" viewBox="0 0 10 16"><rect x="1" y="1" width="8" height="14" rx="1.5" fill="none" stroke="#fff" stroke-width="1.6"/><circle cx="5" cy="12" r="1" fill="#fff"/></svg>
</div>
<div class="abs contact-text" style="left:635px;top:2033px"><b>PHONE:</b>1800 4141 7272</div>
<div class="abs contact-icon" style="left:578px;top:2098px">
  <svg width="16" height="12" viewBox="0 0 16 12"><rect x="1" y="1" width="14" height="10" rx="1" fill="#fff"/><path d="M1 1l7 5 7-5" fill="none" stroke="#1e1e1e" stroke-width="1.4"/></svg>
</div>
<div class="abs contact-text" style="left:635px;top:2094px"><b>Mail:</b>info@varlomex.com</div>

<div class="abs col-title" style="left:813px;top:1895px">CONTACT FORM</div>
<div class="abs col-rule" style="left:813px;top:1932px;width:104px"></div>
<div class="abs field" style="left:813px;top:1952px;width:138px;height:35px">Name</div>
<div class="abs field" style="left:960px;top:1952px;width:141px;height:35px">Phone</div>
<div class="abs field" style="left:813px;top:1994px;width:288px;height:66px">Message</div>
<div class="abs send">SEND MESSAGE</div>
</footer>

<div class="abs bottombar"></div>
<div class="abs copyright">Copyright © 2016 Varlomex. All Right Reserved</div>
<div class="abs social-bottom"><span></span><span></span><span></span><span></span></div>

</body>
</html>
```